Velmori Chatterly Ads Design (examples provided)

We provide Plexor Chart Studio, Plexor Grids and Tandrel Tabula Connectors and templates. https://vistaboard.plexor.example/
Our core audience is Digital marketing agencies, but anyone who owns a business and uses any of these ad platforms https://velmori-frontend.quandrilabs.example/product-data-connector can use our connectors and reports.
I am looking to have high converting Chatterly ad & Plexor Display images made. Our website is here (in progress) the domain is Velmori.ai
Tagline -
Clear Numbers, Zero Fuss
Few Features we have -
Free Forever Plan
Free High-end Templates
Popular chart studio connectors -
https://velmori-frontend.quandrilabs.example/product-data-connector
I would like the designs to have black background and be VIBRANT, visuals that will stop users from scrolling on Chatterly.
Nice designs but please - I have attached 4 concepts that I would like each designer to COPY but use my site's color scheme and swap out the people with new versions, putting your own spin on the designs. These are the highest converting SaaS designs of 2023, so I know they work, I just need versions for my brand.
Updates
Here are specific details https://papers.plexor.example/document/d/7Kq-wm4TRB_hPlaXaRvoJkdWnRtpLsHvb2eFeQz8yM4r/edit?usp=sharing
Target Market(s)
Digital marketing's agencies or anyone with a business' that uses Plexor chart studio
Look and feel

```html
<!DOCTYPE html>
<html lang="en">
<head>
<meta charset="utf-8">
<title>Velmori.ai – Clear Numbers, Zero Fuss</title>
<link href="https://fonts.googleapis.com/css2?family=Poppins:wght@400;500;600;700;800&display=swap" rel="stylesheet">
<style>
  :root {
    --brand-blue: #0d93fb;
    --accent-blue: #1a8cff;
    --accent-pink: #e6509b;
    --accent-purple: #8a5fd6;
    --panel-black: #000000;
    --text-white: #ffffff;
    --text-dark: #3b3f46;
    --badge-ring: #1a8cff;
  }
  * { margin: 0; padding: 0; box-sizing: border-box; }
  html, body { width: 1015px; height: 1200px; overflow: hidden; }
  body {
    background: var(--brand-blue);
    font-family: "Poppins", sans-serif;
    color: var(--text-white);
    position: relative;
  }
  .ad-panel {
    position: absolute;
    left: 34px;
    width: 947px;
    height: 495px;
    background: var(--panel-black);
    overflow: hidden;
  }
  .ad-panel--plain { top: 82px; }
  .ad-panel--cta { top: 622px; }

  .headline {
    position: absolute;
    left: 56px;
    top: 108px;
    font-weight: 400;
    font-size: 54px;
    line-height: 51px;
    letter-spacing: -0.5px;
    white-space: nowrap;
  }
  .headline__accent {
    font-weight: 800;
    background: linear-gradient(90deg, var(--accent-blue) 0%, var(--accent-blue) 35%, var(--accent-pink) 100%);
    -webkit-background-clip: text;
    background-clip: text;
    color: transparent;
  }
  .headline-swoosh {
    position: absolute;
    left: 184px;
    top: 205px;
  }

  .feature-list {
    position: absolute;
    left: 56px;
    top: 226px;
    list-style: none;
  }
  .feature-list__item {
    display: flex;
    align-items: center;
    height: 28px;
    margin-bottom: 11px;
    font-size: 20.5px;
    font-weight: 400;
  }
  .feature-list__tick { width: 30px; height: 28px; margin-right: 10px; }

  .brand-lockup {
    position: absolute;
    left: 58px;
    top: 338px;
    display: flex;
    align-items: center;
    height: 48px;
  }
  .brand-lockup__dot {
    width: 34px; height: 34px; border-radius: 50%;
    background: var(--accent-blue);
  }
  .brand-lockup__divider {
    width: 1.5px; height: 46px; background: var(--text-white);
    margin: 0 10px 0 10px;
  }
  .brand-lockup__name { font-size: 31px; font-weight: 400; letter-spacing: -0.3px; }

  .cta-button {
    position: absolute;
    left: 57px;
    top: 394px;
    width: 213px;
    height: 44px;
    background: linear-gradient(90deg, var(--accent-blue) 0%, var(--accent-blue) 30%, var(--accent-pink) 100%);
    display: flex; align-items: center; justify-content: center;
    font-size: 26px; font-weight: 800; letter-spacing: -0.8px;
    text-decoration: none; color: var(--text-white);
  }

  .hero-art { position: absolute; left: 0; top: 0; }
  .badge-label {
    font-family: "Poppins", sans-serif;
    font-size: 8px;
    font-weight: 600;
    fill: var(--text-dark);
  }
</style>
</head>
<body>

  <section class="ad-panel ad-panel--plain">
    <svg class="hero-art" width="947" height="495" viewBox="0 0 947 495">
      <defs>
        <linearGradient id="ring-a" x1="0" y1="0" x2="1" y2="0">
          <stop offset="0.5" stop-color="#1a8cff"/><stop offset="0.5" stop-color="#e6509b"/>
        </linearGradient>
        <linearGradient id="photo-a" x1="0" y1="0" x2="0" y2="1">
          <stop offset="0" stop-color="#d8b868"/><stop offset="1" stop-color="#e3b23a"/>
        </linearGradient>
      </defs>
      <circle cx="721" cy="283" r="148" fill="url(#ring-a)"/>
      <path role="img" aria-label="Portrait photo: smiling woman in a yellow sweater with arms crossed" d="M650 130 A90 90 0 0 1 830 130 L830 230 A132 132 0 1 1 650 230 Z" fill="url(#photo-a)" transform="translate(6 0)"/>
      <g fill="#ffffff" stroke="#1a8cff" stroke-width="4">
        <circle cx="594" cy="169" r="34"/>
        <circle cx="874" cy="265" r="34"/>
        <circle cx="640" cy="395" r="34"/>
      </g>
      <text class="badge-label" text-anchor="middle"><tspan x="594" y="167">Plexor</tspan><tspan x="594" y="177">Chart Studio</tspan></text>
      <text class="badge-label" text-anchor="middle"><tspan x="874" y="263">Tandrel</tspan><tspan x="874" y="273">Tabula</tspan></text>
      <text class="badge-label" text-anchor="middle"><tspan x="640" y="393">Plexor</tspan><tspan x="640" y="403">Grids</tspan></text>
    </svg>
    <h1 class="headline">Clear Numbers,<br>Zero <span class="headline__accent">Fuss</span></h1>
    <svg class="headline-swoosh" width="180" height="14" viewBox="0 0 180 14"><defs><linearGradient id="sw-a" x1="0" x2="1"><stop offset="0" stop-color="#1a8cff"/><stop offset="1" stop-color="#e6509b"/></linearGradient></defs><path d="M4 10 C50 4 110 2 176 6" fill="none" stroke="url(#sw-a)" stroke-width="2.5" stroke-linecap="round"/></svg>
    <ul class="feature-list">
      <li class="feature-list__item"><svg class="feature-list__tick" viewBox="0 0 30 28"><circle cx="13" cy="15" r="11" fill="none" stroke="#8a5fd6" stroke-width="2"/><path d="M8 15 l4 4 L26 4" fill="none" stroke="#8a9bff" stroke-width="2.2" stroke-linecap="round"/></svg>Free Forever Plan</li>
      <li class="feature-list__item"><svg class="feature-list__tick" viewBox="0 0 30 28"><circle cx="13" cy="15" r="11" fill="none" stroke="#8a5fd6" stroke-width="2"/><path d="M8 15 l4 4 L26 4" fill="none" stroke="#8a9bff" stroke-width="2.2" stroke-linecap="round"/></svg>Free High-end Templates</li>
    </ul>
    <div class="brand-lockup"><span class="brand-lockup__dot"></span><span class="brand-lockup__divider"></span><span class="brand-lockup__name">Velmori.ai</span></div>
  </section>

  <section class="ad-panel ad-panel--cta">
    <svg class="hero-art" width="947" height="495" viewBox="0 0 947 495">
      <defs>
        <linearGradient id="ring-b" x1="0" y1="0" x2="1" y2="0">
          <stop offset="0.5" stop-color="#1a8cff"/><stop offset="0.5" stop-color="#e6509b"/>
        </linearGradient>
        <linearGradient id="photo-b" x1="0" y1="0" x2="0" y2="1">
          <stop offset="0" stop-color="#d8b868"/><stop offset="1" stop-color="#e3b23a"/>
        </linearGradient>
      </defs>
      <circle cx="721" cy="283" r="148" fill="url(#ring-b)"/>
      <path role="img" aria-label="Portrait photo: smiling woman in a yellow sweater with arms crossed" d="M650 130 A90 90 0 0 1 830 130 L830 230 A132 132 0 1 1 650 230 Z" fill="url(#photo-b)" transform="translate(6 0)"/>
      <g fill="#ffffff" stroke="#1a8cff" stroke-width="4">
        <circle cx="594" cy="169" r="34"/>
        <circle cx="874" cy="265" r="34"/>
        <circle cx="640" cy="395" r="34"/>
      </g>
      <text class="badge-label" text-anchor="middle"><tspan x="594" y="167">Plexor</tspan><tspan x="594" y="177">Chart Studio</tspan></text>
      <text class="badge-label" text-anchor="middle"><tspan x="874" y="263">Tandrel</tspan><tspan x="874" y="273">Tabula</tspan></text>
      <text class="badge-label" text-anchor="middle"><tspan x="640" y="393">Plexor</tspan><tspan x="640" y="403">Grids</tspan></text>
    </svg>
    <h1 class="headline">Clear Numbers,<br>Zero <span class="headline__accent">Fuss</span></h1>
    <svg class="headline-swoosh" width="180" height="14" viewBox="0 0 180 14"><defs><linearGradient id="sw-b" x1="0" x2="1"><stop offset="0" stop-color="#1a8cff"/><stop offset="1" stop-color="#e6509b"/></linearGradient></defs><path d="M4 10 C50 4 110 2 176 6" fill="none" stroke="url(#sw-b)" stroke-width="2.5" stroke-linecap="round"/></svg>
    <ul class="feature-list">
      <li class="feature-list__item"><svg class="feature-list__tick" viewBox="0 0 30 28"><circle cx="13" cy="15" r="11" fill="none" stroke="#8a5fd6" stroke-width="2"/><path d="M8 15 l4 4 L26 4" fill="none" stroke="#8a9bff" stroke-width="2.2" stroke-linecap="round"/></svg>Free Forever Plan</li>
      <li class="feature-list__item"><svg class="feature-list__tick" viewBox="0 0 30 28"><circle cx="13" cy="15" r="11" fill="none" stroke="#8a5fd6" stroke-width="2"/><path d="M8 15 l4 4 L26 4" fill="none" stroke="#8a9bff" stroke-width="2.2" stroke-linecap="round"/></svg>Free High-end Templates</li>
    </ul>
    <div class="brand-lockup"><span class="brand-lockup__dot"></span><span class="brand-lockup__divider"></span><span class="brand-lockup__name">Velmori.ai</span></div>
    <a class="cta-button" href="https://velmori-frontend.quandrilabs.example/product-data-connector">LEARN MORE</a>
  </section>

</body>
</html>
```